Business Card: RW Office Partners - Your organised problem solver

Business Name: RW Office Partners
Website: www.rwofficepartners.com.au
Email: marisol@rwofficepartners.com.au
Mobile: 61 482 907 236
Facebook: @rwofficepartners
Instrgram: @rwofficepartners

Brading Colours:
HEX
#986474
#ddccd3
#7a8498
#c9d8e4
#000000
#ffffff

Tag Line: Clear desks, calm days ahead

Link to DRAFT website:
https://deskhelpcollective.wixsite.com/rw-office-partners

About Page from the website:
My name is Marisol Wrenfield, and I would love to assist you to become more productive in your day to day and achieve your business and personal goals.
My mission is to give you time, time to work on the important tasks of your business or to be able to spend more time with your family. I will take on the tasks you don’t have time for, don’t know well or simply don’t like to do.
I have an extensive background in Administration, Tender Coordination, Document Control, WHS and Quality Management working primarily in the Construction, Mining and Corporate World.
I am passionate about being organised, having order and making things in your life (and mine) easier! I love to watch something unfold and grow into something amazing! I am known for being the go-to problem solver, the organiser of all things, producing high standards of work even under pressure. I’m also a confident communicator, and I understand that you’re busy running your business.

Target Market(s)

Small to Medium Business who require assistance in their business by a virtual assistant.

Industry/Entity Type

Virtual Assistant

Contact Information for Business Card

Mobile: 61 482 907 236

Font styles to use
Sans Serif

Colors
ffffff

Requirements
Must have
• Branding Colours as outlined.
Contact Details as outlined.
Logo as provided.
Proper contact details - mobile, facebook, instragm, website.
Simple, Elegant, very clean looking.
Should not have
• Note cute with pictures.
Not too girly as still want to market to construction companies.

```html
<!DOCTYPE html>
<html lang="en">
<head>
<meta charset="utf-8">
<title>RW Office Partners – Business Card</title>
<link rel="stylesheet" href="https://fonts.googleapis.com/css2?family=Montserrat:wght@500;600&family=Roboto:ital,wght@0,400;0,500;1,700&display=swap">
<style>
  :root {
    --backdrop: #3b3b3e;
    --card: #1c1b1f;
    --rose: #986474;
    --rose-light: #ddccd3;
    --slate: #7a8498;
    --emboss: #5e5e64;
    --tagline: #4a4952;
    --white: #ffffff;
  }
  * { margin: 0; padding: 0; box-sizing: border-box; }
  html, body { width: 799px; height: 1200px; overflow: hidden; }
  body {
    background: var(--backdrop);
    font-family: "Roboto", Arial, sans-serif;
    color: var(--white);
    position: relative;
  }
  .card {
    position: absolute;
    left: 80px;
    width: 640px;
    height: 366px;
    background: var(--card);
    border-radius: 3px;
  }
  .card--front { top: 150px; }
  .card--back { top: 690px; }

  .brand-name {
    font-family: "Montserrat", Arial, sans-serif;
    font-weight: 600;
    letter-spacing: 0.02em;
    white-space: nowrap;
  }
  .card--front .brand-name {
    position: absolute;
    left: 0; right: 0; top: 120px;
    text-align: center;
    font-size: 46px;
    color: var(--emboss);
  }

  .social { list-style: none; font-size: 17px; }
  .social li { display: flex; align-items: center; gap: 10px; white-space: nowrap; }
  .social .mark {
    width: 14px; height: 14px;
    border-radius: 3px;
    background: var(--rose);
    flex: none;
  }
  .card--front .social {
    position: absolute;
    left: 110px; top: 262px;
    display: flex; gap: 26px;
  }

  .card--back .brand-block {
    position: absolute;
    right: 40px; top: 48px;
    text-align: right;
  }
  .card--back .brand-name { font-size: 32px; color: var(--slate); }
  .tagline {
    margin-top: 6px;
    font-family: "Montserrat", Arial, sans-serif;
    font-weight: 500;
    font-size: 11px;
    letter-spacing: 0.28em;
    text-transform: uppercase;
    color: var(--tagline);
    white-space: nowrap;
  }

  .person { position: absolute; left: 44px; top: 150px; }
  .person__name { font-size: 22px; font-weight: 700; font-style: italic; color: var(--rose); }
  .person__role { font-size: 15px; margin-top: 4px; }

  .contact { list-style: none; position: absolute; left: 44px; top: 222px; font-size: 15px; }
  .contact li { display: flex; align-items: center; gap: 12px; margin-bottom: 8px; white-space: nowrap; }
  .contact svg { width: 14px; height: 14px; flex: none; fill: var(--rose); }

  .divider {
    position: absolute;
    left: 300px; right: 40px; top: 196px;
    height: 1px;
    background: var(--slate);
  }
  .card--back .social { position: absolute; right: 44px; top: 262px; }
  .card--back .social li { margin-bottom: 10px; }
</style>
</head>
<body>
  <section class="card card--front" aria-label="Card front">
    <div class="brand-name">RW Office Partners</div>
    <ul class="social">
      <li><span class="mark"></span>@rwofficepartners</li>
      <li><span class="mark"></span>@rwofficepartners</li>
    </ul>
  </section>

  <section class="card card--back" aria-label="Card back">
    <div class="brand-block">
      <div class="brand-name">RW Office Partners</div>
      <div class="tagline">Clear desks, calm days ahead</div>
    </div>

    <div class="person">
      <div class="person__name">Marisol Wrenfield</div>
      <div class="person__role">Virtual Assistant</div>
    </div>

    <ul class="contact">
      <li>
        <svg viewBox="0 0 16 16" aria-hidden="true"><path d="M3 1h3l1.5 4-2 1.5a9 9 0 0 0 4 4L11 8.5l4 1.5v3a2 2 0 0 1-2 2A12 12 0 0 1 1 3a2 2 0 0 1 2-2z"/></svg>
        61 482 907 236
      </li>
      <li>
        <svg viewBox="0 0 16 16" aria-hidden="true"><path d="M1 3h14v10H1z"/><path d="M1 3l7 6 7-6" fill="none" stroke="#1c1b1f" stroke-width="1.5"/></svg>
        marisol@rwofficepartners.com.au
      </li>
      <li>
        <svg viewBox="0 0 16 16" aria-hidden="true"><circle cx="8" cy="8" r="7"/><path d="M1 8h14M8 1c-3 3-3 11 0 14M8 1c3 3 3 11 0 14" fill="none" stroke="#1c1b1f" stroke-width="1"/></svg>
        www.rwofficepartners.com.au
      </li>
    </ul>

    <div class="divider"></div>

    <ul class="social">
      <li><span class="mark"></span>@rwofficepartners</li>
      <li><span class="mark"></span>@rwofficepartners</li>
    </ul>
  </section>
</body>
</html>
```